Expedition Cruise Sales Website for the Polar Regions (Antarctica & Arctic)

This will be a website for selling cruises.
This site should have a homepage, a ship page, destinations, and itineraries.
I have created a file specifying each page, and it is attached.
Pages:
1. Home
2. Cruise Lines
- 2.1 Ships
3. Destinations
- 3.1 Region - 3.2 Country - 3.3 City
4. Itineraries
- 4.1 Itinerary
5. Blog / Travel Tips 6. About Us
7. Contact
Please take a look on the attached pdf
Target Market(s)
Expedition Travelers
Coding
Coded - Design and coding required
Number of Pages Required
5+ page
Font styles to use
Look and feel
Each slider illustrates characteristics of the customer's brand and the style your logo design should communicate.

```html
<!DOCTYPE html>
<html lang="en">
<head>
<meta charset="UTF-8">
<title>Floenmark.co — Luxury Expedition Cruises</title>
<link href="https://fonts.googleapis.com/css2?family=Lato:wght@300;400;700&family=Crimson+Pro:wght@400;500&display=swap" rel="stylesheet">
<style>
:root{
  --navy:#0c1226;
  --ink:#1b2333;
  --muted:#4d5566;
  --blue:#3b82d0;
  --blue-light:#7fbff0;
  --gold:#f0b429;
  --white:#ffffff;
  --line:#d9dee6;
  --shadow:0 10px 28px rgba(30,60,110,.12);
}
*{box-sizing:border-box;margin:0;padding:0}
html,body{width:1200px;height:4069px;overflow:hidden}
body{position:relative;font-family:"Crimson Pro",Georgia,serif;color:var(--ink);background:var(--white)}
.sans{font-family:"Lato",Arial,sans-serif}
.abs{position:absolute}
.btn{font-family:"Lato",Arial,sans-serif;font-size:13px;border-radius:20px;display:inline-flex;align-items:center;justify-content:center;gap:6px;white-space:nowrap}
.btn-solid{background:linear-gradient(90deg,var(--blue),var(--blue-light));color:var(--white)}
.btn-outline{border:1px solid var(--blue);color:var(--blue)}
.eyebrow{font-family:"Lato",Arial,sans-serif;font-size:11px;color:var(--blue)}
.h2{font-family:"Lato",Arial,sans-serif;font-weight:400;text-transform:uppercase;font-size:42px;line-height:1.15;color:var(--ink)}
.lead{font-size:14px;color:var(--muted)}

.hero{position:absolute;left:0;top:0;width:1200px;height:685px;background:linear-gradient(180deg,#0a1030 0%,#14204a 45%,#1b2e55 70%,#0b1224 100%);color:var(--white)}
.nav{position:absolute;top:0;left:100px;width:1000px;height:63px;display:flex;align-items:center}
.brand{font-family:"Lato",Arial,sans-serif;font-weight:700;font-size:17px;display:flex;align-items:center;gap:8px}
.brand .dot{width:14px;height:14px;border-radius:50%;background:currentColor}
.menu{margin-left:auto;display:flex;gap:14px;font-family:"Lato",Arial,sans-serif;font-size:12.5px;align-items:center}
.menu .active{color:var(--gold)}
.menu .btn{height:34px;padding:0 20px}
.hero-title{position:absolute;top:196px;left:0;width:1200px;text-align:center;font-family:"Lato",Arial,sans-serif;font-size:50px;line-height:63px;font-weight:400}
.hero-sub{position:absolute;top:334px;width:1200px;text-align:center;font-size:14px;opacity:.9}
.perks{position:absolute;top:420px;left:100px;width:1000px;display:flex}
.perk{flex:1;text-align:center}
.perk svg{width:30px;height:30px;stroke:#fff;fill:none;stroke-width:1.5}
.perk h3{font-family:"Lato",Arial,sans-serif;font-weight:400;font-size:17px;margin:14px 0 6px}
.perk p{font-size:13.5px;line-height:1.45;opacity:.85;padding:0 4px}
.search{position:absolute;top:644px;left:100px;width:1000px;height:80px;background:var(--white);border-radius:40px;box-shadow:var(--shadow);display:flex;align-items:center;padding:0 22px 0 40px;gap:22px}
.field{width:248px}
.field label{display:block;font-family:"Lato",Arial,sans-serif;font-size:11px;color:var(--blue);margin-bottom:10px}
.field div{font-size:13px;color:#888;border-bottom:1px solid var(--line);padding-bottom:6px;display:flex;justify-content:space-between}
.field div.set{color:var(--ink)}
.search .btn{height:42px;padding:0 26px;margin-left:auto}

.card{position:absolute;border-radius:16px;overflow:hidden;color:var(--white);box-shadow:var(--shadow)}
.card .ph{position:absolute;inset:0}
.card h3{position:absolute;top:22px;left:14px;right:14px;font-family:"Lato",Arial,sans-serif;font-weight:400;text-transform:uppercase;font-size:27px;line-height:1.15}
.card .desc{position:absolute;left:14px;font-size:13.5px;line-height:1.45}
.card .price{position:absolute;right:14px;text-align:right;font-size:12.5px;line-height:1.1}
.card .price b{display:block;font-family:"Lato",Arial,sans-serif;font-weight:400;font-size:20px}
.card .bar{position:absolute;left:0;right:0;bottom:0;height:44px;background:linear-gradient(90deg,var(--blue),var(--blue-light));display:flex;align-items:center;justify-content:center;font-family:"Lato",Arial,sans-serif;font-size:13px;gap:6px}

.band{position:absolute;left:0;width:1200px;overflow:hidden;color:var(--white)}
.band .h2{color:var(--white)}
.arrow{position:absolute;width:38px;height:38px;border-radius:50%;display:flex;align-items:center;justify-content:center}
.arrow.ghost{border:1px solid rgba(255,255,255,.8)}
.arrow.fill{background:var(--blue)}
.arrow svg{width:14px;height:14px;stroke:#fff;fill:none;stroke-width:2}

.dest h3{font-size:20px;top:18px}
.line h3{font-size:20px;top:64px}
.line .ico{position:absolute;top:20px;left:14px;width:28px;height:28px;stroke:#fff;fill:none;stroke-width:1.4}
.rating{position:absolute;top:118px;left:14px;font-family:"Lato",Arial,sans-serif;font-size:12px;color:var(--gold)}

.quote{position:absolute;border:2px solid rgba(255,255,255,.85);border-radius:16px;background:rgba(255,255,255,.14);color:var(--white);padding:28px 18px}
.quote .mark{font-family:"Lato",Arial,sans-serif;font-weight:700;font-size:54px;line-height:40px;color:var(--blue)}
.quote p{font-size:13.5px;margin-top:6px;line-height:1.45}
.quote .who{position:absolute;bottom:30px;left:18px;right:18px;display:flex;align-items:center;gap:10px;font-size:13.5px}
.quote .avatar{width:36px;height:36px;border-radius:50%;background:#6f8a7a}
.quote .stars{margin-left:auto;color:var(--gold);letter-spacing:5px;font-size:13px}

.news{position:absolute;top:3016px;left:100px;width:1000px;height:107px;border-radius:16px;box-shadow:var(--shadow);background:var(--white);padding:24px 20px}
.news label{font-family:"Lato",Arial,sans-serif;font-size:11px;display:block;margin-bottom:14px}
.news .input{width:790px;border-bottom:1px solid var(--line);padding-bottom:6px;font-size:13px;color:#888}
.news .btn{position:absolute;right:20px;top:38px;height:42px;padding:0 28px}

.footer{position:absolute;top:3723px;left:0;width:1200px;height:346px}
.fcol{position:absolute;top:78px;font-size:13.5px;color:var(--muted);line-height:30px}
.fcol h4{font-family:"Lato",Arial,sans-serif;font-weight:400;font-size:12.5px;color:var(--ink);margin-bottom:6px}
.fcol svg{width:14px;height:14px;stroke:var(--blue);fill:none;stroke-width:1.6;vertical-align:-2px;margin-right:6px}
.social{display:flex;gap:14px;margin-top:10px}
.social span{width:34px;height:34px;border-radius:50%;border:1px solid var(--blue);display:flex;align-items:center;justify-content:center}
.social span i{width:10px;height:10px;border-radius:50%;background:var(--blue)}
.legal{position:absolute;top:287px;left:100px;width:1000px;border-top:1px solid var(--line);padding-top:18px;font-size:13px;color:var(--muted);display:flex}
.legal .links{margin-left:auto;display:flex;gap:20px}
</style>
</head>
<body>

<header class="hero">
  <div role="img" aria-label="Night view of a luxury cruise ship lit up in harbor" class="abs" style="inset:0;background:radial-gradient(ellipse at 55% 55%,rgba(90,120,200,.35),transparent 60%)"></div>
  <nav class="nav">
    <div class="brand"><span class="dot"></span>Floenmark.co</div>
    <div class="menu">
      <span class="active">Home</span><span>About Us</span><span>Cruise Lines</span><span>Destinations</span><span>Itineraries</span><span>Blog/Travel Tips</span>
      <span class="btn btn-solid">Contact</span>
      <span class="btn" style="border:1px solid #7fbff0;color:#fff">Book Now</span>
    </div>
  </nav>
  <h1 class="hero-title">UNFORGETTABLE JOURNEYS AWAIT –<br>SET SAIL IN LUXURY</h1>
  <p class="hero-sub">Discover world-class cruise experiences, from the Arctic to the tropics. Find your perfect voyage today.</p>
  <div class="perks">
    <div class="perk"><svg viewBox="0 0 30 30"><path d="M15 3v24M20 9c-1-2-3-3-5-3-3 0-5 2-5 4 0 5 10 3 10 9 0 2-2 4-5 4-3 0-5-1-6-3"/></svg><h3>Best Price Guarantee</h3><p>Exclusive rates and special discounts you won't find anywhere else.</p></div>
    <div class="perk"><svg viewBox="0 0 30 30"><path d="M4 20h22l-3 6H7zM8 20v-7h14v7M11 13V8h8v5M14 8V4"/></svg><h3>Expert Travel Advisors</h3><p>Our cruise specialists help you find the perfect itinerary tailored to your needs.</p></div>
    <div class="perk"><svg viewBox="0 0 30 30"><path d="M6 18v-4a9 9 0 0 1 18 0v4M6 17h3v7H6zM21 17h3v7h-3z"/></svg><h3>24/7 Customer Support</h3><p>Seamless booking experience with round-the-clock assistance.</p></div>
    <div class="perk"><svg viewBox="0 0 30 30"><rect x="3" y="7" width="24" height="16" rx="2"/><path d="M3 12h24M7 18h6"/></svg><h3>Flexible Payment Options</h3><p>Secure your trip today with easy installment plans.</p></div>
  </div>
</header>

<form class="search">
  <div class="field"><label>DESTINATION</label><div class="set">Carribean <span>⌄</span></div></div>
  <div class="field"><label>DEPARTURE</label><div>Choose Departure Port <span>⌄</span></div></div>
  <div class="field"><label>DATE</label><div>Choose Departure Date <span>⌄</span></div></div>
  <span class="btn btn-solid">Find Cruises</span>
</form>

<section>
  <p class="eyebrow abs" style="top:794px;width:1200px;text-align:center">Featured Offers</p>
  <h2 class="h2 abs" style="top:810px;width:1200px;text-align:center">Exclusive Cruise Deals – Limited Time Offers</h2>
  <p class="lead abs" style="top:866px;width:1200px;text-align:center">Handpicked cruise experiences at unbeatable prices. Secure your spot before they're gone!</p>

  <article class="card" style="left:100px;top:917px;width:320px;height:333px">
    <div class="ph" role="img" aria-label="Antarctic glacier ice wall" style="background:linear-gradient(160deg,#dfeef8,#9cc3dd 50%,#3e6e94)"></div>
    <h3>Best Antarctic Cruises</h3>
    <p class="desc" style="bottom:66px;width:200px">Sail through icy wonders and witness breathtaking wildlife in Antarctica.</p>
    <p class="price" style="bottom:70px">From<b>$4,999</b></p>
    <div class="bar">View Offer ↗</div>
  </article>
  <article class="card" style="left:440px;top:917px;width:320px;height:333px">
    <div class="ph" role="img" aria-label="Cruise ship near Galápagos islands" style="background:linear-gradient(180deg,#2f6f8c,#4d8aa0 40%,#2c4a5a 75%,#1f3340)"></div>
    <h3>Top Galápagos Cruises</h3>
    <p class="desc" style="bottom:20px;width:200px">Explore the pristine islands where nature thrives, guided by experts.</p>
    <p class="price" style="bottom:22px">From<b>$3,799</b></p>
  </article>
  <article class="card" style="left:780px;top:917px;width:320px;height:333px">
    <div class="ph" role="img" aria-label="Tropical bay with boats and green hills" style="background:linear-gradient(180deg,#3f6f52,#2b7fa8 45%,#1f6d9a 80%,#355c6e)"></div>
    <h3>Last-Minute Deals</h3>
    <p class="desc" style="bottom:20px;width:190px">Spontaneous adventure? Book now for incredible discounts on luxury cruises.</p>
    <p class="price" style="bottom:22px">Up to<b>40% OFF</b></p>
  </article>
</section>

<section class="band" style="top:1317px;height:467px">
  <div role="img" aria-label="Cruise ship docked beside forested mountains" class="abs" style="inset:0;background:linear-gradient(180deg,#3c4750,#5a6670 35%,#4a5866 65%,#2e3d4c)"></div>
  <h2 class="h2 abs" style="left:100px;top:66px;width:370px;font-size:40px;line-height:49px">Explore the World, One Cruise at a Time</h2>
  <p class="abs" style="left:100px;top:218px;width:420px;font-size:13.5px;line-height:1.45">From sun-drenched Caribbean beaches to the mystical fjords of Norway, your dream cruise starts here.</p>
  <span class="arrow ghost" style="left:99px;top:362px"><svg viewBox="0 0 14 14"><path d="M9 2 4 7l5 5"/></svg></span>
  <span class="arrow fill" style="left:155px;top:362px"><svg viewBox="0 0 14 14"><path d="M5 2l5 5-5 5"/></svg></span>

  <article class="card dest" style="left:610px;top:68px;width:235px;height:328px">
    <div class="ph" role="img" aria-label="Mediterranean coastal cliffs and sea" style="background:linear-gradient(180deg,#9fb3c2,#4f6f5f 45%,#2d5a74 80%)"></div>
    <h3>Mediterranean Wonders</h3>
    <p class="desc" style="bottom:56px;width:210px">Historic cities, crystal-clear waters, and rich culture.</p>
    <div class="bar">View Destination ↗</div>
  </article>
  <article class="card dest" style="left:865px;top:68px;width:235px;height:328px">
    <div class="ph" role="img" aria-label="Caribbean palm trees at sunset" style="background:linear-gradient(180deg,#5a8fb8,#c9a25a 50%,#6a5a3a 85%)"></div>
    <h3>Caribbean Paradise</h3>
    <p class="desc" style="bottom:14px;width:210px">Swaying palm trees, turquoise waters, and endless relaxation.</p>
  </article>
  <article class="card dest" style="left:1120px;top:68px;width:235px;height:328px">
    <div class="ph" role="img" aria-label="Alaskan glacier landscape" style="background:linear-gradient(180deg,#8fb0c8,#5d7f96 50%,#34526a)"></div>
    <h3>Alaskan Adventures</h3>
    <p class="desc" style="bottom:14px;width:210px">Majestic glaciers, wildlife encounters, and vast landscapes.</p>
  </article>
</section>

<section>
  <p class="eyebrow abs" style="left:100px;top:1853px">Cruise Lines</p>
  <h2 class="h2 abs" style="left:100px;top:1868px;width:760px;font-size:40px;line-height:48px">Discover the World's Leading Cruise Lines</h2>
  <p class="lead abs" style="left:100px;top:1973px">Explore top-rated cruise lines and their world-class fleets.</p>
  <span class="btn btn-solid abs" style="left:924px;top:1950px;width:176px;height:40px">See All Cruise Lines</span>

  <article class="card line" style="left:100px;top:2024px;width:235px;height:333px">
    <div class="ph" role="img" aria-label="Large white cruise ship under blue sky" style="background:linear-gradient(180deg,#7fa9d6,#b7c9dc 50%,#5d7e9c)"></div>
    <svg class="ico" viewBox="0 0 28 28"><circle cx="14" cy="12" r="5"/><path d="M14 2v4M14 18v4M4 12h4M20 12h4M4 25h20"/></svg>
    <h3>Ocean Elegance Cruises</h3><span class="rating">★ 4.9</span>
    <p class="desc" style="bottom:64px;width:210px">Luxury meets innovation with award-winning service, all-suite accommodations, and curated gourmet dining.</p>
    <div class="bar">View Cruise ↗</div>
  </article>
  <article class="card line" style="left:355px;top:2024px;width:235px;height:333px">
    <div class="ph" role="img" aria-label="Cruise ship at a port at dusk" style="background:linear-gradient(180deg,#6b7fa5,#b98aa0 45%,#4c4a66 85%)"></div>
    <svg class="ico" viewBox="0 0 28 28"><circle cx="14" cy="14" r="3"/><path d="M14 4v7M14 17v7M4 14h7M17 14h7M7 7l5 5M16 16l5 5M21 7l-5 5M12 16l-5 5"/></svg>
    <h3>Grand Horizon Voyages</h3><span class="rating">★ 4.8</span>
    <p class="desc" style="bottom:20px;width:210px">A refined cruising experience with immersive cultural excursions, spacious cabins, and world-class entertainment.</p>
  </article>
  <article class="card line" style="left:610px;top:2024px;width:235px;height:333px">
    <div class="ph" role="img" aria-label="Harbor city lights at night" style="background:linear-gradient(180deg,#3b2f2c,#6b4a36 50%,#1f1a1c)"></div>
    <svg class="ico" viewBox="0 0 28 28"><path d="M4 20h20l-3 4H7zM8 20l3-8h9l2 8M14 12V5M4 26h20"/></svg>
    <h3>Celestial Dream Cruises</h3><span class="rating">★ 4.7</span>
    <p class="desc" style="bottom:20px;width:210px">Blending comfort and adventure, Celestial Dream offers breathtaking itineraries with all-inclusive luxury.</p>
  </article>
  <article class="card line" style="left:865px;top:2024px;width:235px;height:333px">
    <div class="ph" role="img" aria-label="Cruise ship at sea under pink sunset" style="background:linear-gradient(180deg,#a0839a,#c7a0a6 45%,#5c5870 80%)"></div>
    <svg class="ico" viewBox="0 0 28 28"><path d="M4 18a10 10 0 0 1 20 0zM14 8v10M9 10l3 8M19 10l-3 8"/></svg>
    <h3>Serenity Voyager Line</h3><span class="rating">★ 4.9</span>
    <p class="desc" style="bottom:20px;width:210px">Unmatched elegance at sea with personalized service, private beach clubs, and exclusive onboard experiences.</p>
  </article>
</section>

<section class="band" style="top:2424px;height:399px">
  <div role="img" aria-label="Cruise ship sailing along a misty coast" class="abs" style="inset:0;background:linear-gradient(180deg,#5d6d7d,#7f8e9c 40%,#465666 75%,#33414f)"></div>
  <h2 class="h2 abs" style="left:100px;top:66px;width:420px;font-size:40px;line-height:49px">What Our Passengers Say</h2>
  <p class="abs" style="left:100px;top:168px;width:390px;font-size:13.5px;line-height:1.45">Real stories from travelers who embarked on the journey of a lifetime.</p>
  <span class="arrow ghost" style="left:99px;top:292px"><svg viewBox="0 0 14 14"><path d="M9 2 4 7l5 5"/></svg></span>
  <span class="arrow fill" style="left:155px;top:292px"><svg viewBox="0 0 14 14"><path d="M5 2l5 5-5 5"/></svg></span>

  <figure class="quote" style="left:610px;top:68px;width:490px;height:265px">
    <div class="mark">“</div>
    <p>Absolutely breathtaking! The service, the food, the destinations – everything was perfect!</p>
    <figcaption class="who"><span class="avatar" role="img" aria-label="Passenger photo"></span>Clara R.<span class="stars">★★★★★</span></figcaption>
  </figure>
  <figure class="quote" style="left:1120px;top:68px;width:490px;height:265px">
    <div class="mark">“</div>
    <p>An unforgettable voyage that exceeded every expectation.</p>
    <figcaption class="who"><span class="avatar" role="img" aria-label="Passenger photo" style="background:#b07a78"></span>James T.</figcaption>
  </figure>
</section>

<section>
  <p class="eyebrow abs" style="top:2894px;width:1200px;text-align:center">Newsletter Subscription</p>
  <h2 class="h2 abs" style="top:2910px;width:1200px;text-align:center">Stay Updated with Exclusive Cruise Deals!</h2>
  <p class="lead abs" style="top:2967px;width:1200px;text-align:center">Sign up for our newsletter and be the first to receive special offers, travel tips, and insider cruise updates.</p>
  <form class="news">
    <label>EMAIL</label>
    <div class="input">Input your email address to subscribe</div>
    <span class="btn btn-solid">Subscribe Now</span>
  </form>
</section>

<section class="band" style="top:3190px;height:533px">
  <div role="img" aria-label="Cruise ship moored at a city harbor" class="abs" style="inset:0;background:linear-gradient(90deg,#8793a3,#5f7387 40%,#415a75 70%,#3a5371)"></div>
  <h2 class="h2 abs" style="left:610px;top:150px;width:480px;font-size:40px;line-height:49px">Have Questions?<br>We're Here to Help!</h2>
  <p class="abs" style="left:610px;top:263px;width:480px;font-size:13.5px;line-height:1.45">Need assistance choosing the perfect cruise? Get in touch with our travel experts for personalized recommendations.</p>
  <span class="btn abs" style="left:610px;top:336px;width:122px;height:40px;background:var(--blue);color:#fff">Contact Us</span>
  <span class="btn abs" style="left:752px;top:336px;width:200px;height:40px;background:#27c24c;color:#fff"><span style="width:13px;height:13px;border:1.5px solid #fff;border-radius:50%"></span>Chat via Live Chat</span>
</section>

<footer class="footer">
  <div class="abs sans" style="left:100px;top:110px;font-size:30px;font-weight:700;color:var(--blue)">Floenmark.co</div>
  <span class="btn btn-outline abs" style="left:100px;top:180px;width:110px;height:36px">Contact Us</span>
  <span class="btn btn-outline abs" style="left:222px;top:180px;width:106px;height:36px">Book Now</span>

  <div class="fcol" style="left:524px"><h4>EXPLORE CRUISE</h4>Cruise Lines<br>Destinations<br>Itineraries<br>Blog/Travel Tips</div>
  <div class="fcol" style="left:695px"><h4>COMPANY</h4>About Us<br>FAQ</div>
  <div class="fcol" style="left:865px;line-height:20px;width:240px">
    <h4 style="margin-bottom:12px">CONTACT INFO</h4>
    88 Harbor Lane, Portview,<br>ME 04101, United States
    <div style="margin-top:10px"><svg viewBox="0 0 14 14"><path d="M3 1h3l1 3-2 1a8 8 0 0 0 4 4l1-2 3 1v3c-6 0-10-4-10-10z"/></svg>(555) 284-9013</div>
    <div style="margin-top:10px"><svg viewBox="0 0 14 14"><rect x="1" y="3" width="12" height="8"/><path d="M1 3l6 5 6-5"/></svg>support@floenmark.co</div>
    <div class="social"><span><i></i></span><span><i></i></span><span><i></i></span></div>
  </div>

  <div class="legal">© 2025 Floenmark.co, All Rights Reserved<div class="links"><span>Privacy Policy</span><span>Terms of Use</span></div></div>
</footer>

</body>
</html>
```